Income Tax Flyer - Updates Needed

Just need to update this flyer design and give it a new look. We would like to keep all the same wording but make it stand out a little more. Our selling point is the "Same Day Tax Advance up to $6,000"

Lending, Small Loans, Tax Services, Title Loans, Personal Loans

```html
<!DOCTYPE html>
<html lang="en">
<head>
<meta charset="utf-8">
<title>Same Day Tax Advance Flyer</title>
<link rel="stylesheet" href="https://fonts.googleapis.com/css2?family=Oswald:wght@600;700&family=Poppins:wght@400;500;600;700;800&display=swap">
<style>
  :root{
    --page:#c4c4c4;
    --green-deep:#0b3b22;
    --green:#0f5a32;
    --green-box:#135a30;
    --red:#c8202a;
    --white:#ffffff;
    --ink:#1b1b1b;
    --gold:#e2b533;
  }
  *{box-sizing:border-box;margin:0;padding:0}
  html,body{width:1200px;height:2778px;overflow:hidden;background:var(--page)}
  .flyer{position:absolute;left:40px;top:528px;width:1120px;height:1722px;background:var(--white);overflow:hidden;box-shadow:0 20px 50px rgba(0,0,0,.25);font-family:'Poppins',sans-serif}
  .flyer-art{position:absolute;left:0;top:0;width:1120px;height:1722px}
  .headline .display{font-family:'Oswald',sans-serif;font-weight:700}
  .headline .upto{font-family:'Poppins',sans-serif;font-weight:500}
  .intro{position:absolute;left:0;width:100%;top:1036px;text-align:center;font-size:44px;font-weight:600;color:var(--ink)}
  .easy-advance{position:absolute;left:0;width:100%;top:1090px;text-align:center;font-size:106px;font-weight:800;line-height:1;letter-spacing:1px}
  .easy-advance .easy{color:var(--red)}
  .easy-advance .advance{color:var(--green)}
  .features{position:absolute;left:110px;top:1287px;width:900px;height:181px;display:flex}
  .feature{position:relative;flex:1;display:flex;align-items:center;justify-content:center;text-align:center;color:var(--white);font-size:31px;line-height:1.2;padding-top:6px}
  .feature b{font-weight:700}
  .feature.green{background:var(--green-box);border-radius:8px}
  .feature.red{background:var(--red);border-radius:8px;z-index:1}
  .feature-icon{position:absolute;top:-82px;left:50%;margin-left:-54px;width:108px;height:108px;border-radius:50%;background:var(--white);display:flex;align-items:center;justify-content:center}
  .feature-icon span{width:86px;height:86px;border-radius:50%;display:flex;align-items:center;justify-content:center}
  .green .feature-icon span{background:var(--green-box)}
  .red .feature-icon span{background:var(--red)}
  .brand{position:absolute;left:60px;top:1548px;display:flex;align-items:center;gap:12px;color:var(--green);font-size:34px;font-weight:600;line-height:1.1}
  .brand-mark{width:26px;height:26px;background:var(--red)}
  .contact-bar{position:absolute;left:381px;top:1528px;width:669px;height:38px;display:flex;border-radius:6px;overflow:hidden;font-weight:700;font-size:25px;color:var(--white)}
  .contact-bar .label{background:var(--green-box);width:360px;display:flex;align-items:center;justify-content:center;letter-spacing:.5px}
  .contact-bar .phone{background:var(--red);flex:1;display:flex;align-items:center;justify-content:center;gap:8px}
  .address{position:absolute;left:400px;top:1568px;font-size:22px;line-height:29px;color:var(--ink);font-style:normal}
  .address .branch{color:var(--red);font-weight:700}
  .address .pin{position:absolute;left:-28px;top:5px}
</style>
</head>
<body>
<main class="flyer">
  <svg class="flyer-art" viewBox="0 0 834 1283" xmlns="http://www.w3.org/2000/svg">
    <defs>
      <radialGradient id="greenGlow" cx="0.5" cy="0.35" r="0.7">
        <stop offset="0" stop-color="#126b3a"/>
        <stop offset="1" stop-color="#08301b"/>
      </radialGradient>
      <linearGradient id="goldFill" x1="0" y1="0" x2="0" y2="1">
        <stop offset="0" stop-color="#c08a18"/>
        <stop offset=".45" stop-color="#f7e27a"/>
        <stop offset=".7" stop-color="#d9a72a"/>
        <stop offset="1" stop-color="#b07a12"/>
      </linearGradient>
      <linearGradient id="silverFill" x1="0" y1="0" x2="0" y2="1">
        <stop offset="0" stop-color="#ffffff"/>
        <stop offset=".55" stop-color="#f1f1f1"/>
        <stop offset=".75" stop-color="#b8b8b8"/>
        <stop offset="1" stop-color="#e6e6e6"/>
      </linearGradient>
      <radialGradient id="coinSoft" cx="0.5" cy="0.5" r="0.5">
        <stop offset="0" stop-color="#e8c44a" stop-opacity=".55"/>
        <stop offset="1" stop-color="#e8c44a" stop-opacity="0"/>
      </radialGradient>
    </defs>

    <rect class="hero-bg" width="834" height="1283" fill="url(#greenGlow)"/>

    <g class="money-art" role="img" aria-label="Falling gold coins and dollar bills">
      <ellipse cx="40" cy="90" rx="60" ry="50" fill="url(#coinSoft)"/>
      <ellipse cx="800" cy="40" rx="70" ry="55" fill="url(#coinSoft)"/>
      <ellipse cx="60" cy="360" rx="80" ry="140" fill="url(#coinSoft)"/>
      <ellipse cx="720" cy="320" rx="70" ry="80" fill="url(#coinSoft)"/>
      <ellipse cx="790" cy="420" rx="50" ry="60" fill="url(#coinSoft)"/>
      <ellipse cx="140" cy="560" rx="120" ry="70" fill="url(#coinSoft)"/>
      <ellipse cx="740" cy="590" rx="90" ry="60" fill="url(#coinSoft)"/>
    </g>

    <path class="swoosh-red" d="M0 828 Q350 640 834 650 L834 727 Q430 660 0 845 Z" fill="var(--red)"/>
    <path class="swoosh-white" d="M0 845 Q430 660 834 727 L834 1283 L0 1283 Z" fill="var(--white)"/>

    <g class="headline">
      <g transform="rotate(-3 408 94)">
        <rect x="242" y="48" width="331" height="92" fill="var(--red)"/>
        <text class="display" x="408" y="122" text-anchor="middle" font-size="66" fill="var(--white)" textLength="296" lengthAdjust="spacingAndGlyphs">SAME DAY</text>
      </g>
      <text class="display" x="403" y="312" text-anchor="middle" font-size="205" fill="url(#goldFill)" textLength="422" lengthAdjust="spacingAndGlyphs">TAX</text>
      <text class="display" x="402" y="476" text-anchor="middle" font-size="193" fill="url(#silverFill)" textLength="449" lengthAdjust="spacingAndGlyphs">ADVANCE</text>
      <text class="upto" x="261" y="517" font-size="32" fill="var(--white)" textLength="76" lengthAdjust="spacingAndGlyphs">UPTO</text>
      <text class="display" x="345" y="603" font-size="145" fill="url(#goldFill)" textLength="288" lengthAdjust="spacingAndGlyphs">$6,000</text>
    </g>
  </svg>

  <p class="intro">File your taxes and apply for an</p>
  <h1 class="easy-advance"><span class="easy">EASY</span> <span class="advance">ADVANCE!</span></h1>

  <section class="features">
    <div class="feature green">
      <div class="feature-icon"><span>
        <svg width="52" height="52" viewBox="0 0 52 52" fill="none" stroke="#fff" stroke-width="5" stroke-linecap="round"><path d="M42 20A17 17 0 0 0 11 16"/><path d="M10 32a17 17 0 0 0 31 4"/><path d="M11 6v11h11"/><path d="M41 46V35H30"/><circle cx="26" cy="26" r="5" fill="#fff" stroke="none"/></svg>
      </span></div>
      <p>Available In<br><b>24 Hours or<br>Less</b></p>
    </div>
    <div class="feature red">
      <div class="feature-icon"><span>
        <svg width="52" height="52" viewBox="0 0 52 52"><circle cx="28" cy="17" r="13" fill="#fff"/><text x="28" y="24" text-anchor="middle" font-size="20" font-weight="700" fill="var(--red)" font-family="Poppins,sans-serif">$</text><path d="M6 38h10l10 4h12l8-6v6l-10 8H6z" fill="#fff"/></svg>
      </span></div>
      <p>Choose Your<br><b>Loan<br>Amount</b></p>
    </div>
    <div class="feature green">
      <div class="feature-icon"><span>
        <svg width="52" height="52" viewBox="0 0 52 52" fill="none" stroke="#fff" stroke-width="4" stroke-linecap="round"><circle cx="31" cy="26" r="15" fill="#fff" stroke="none"/><path d="M31 17v10l6 4" stroke="var(--green-box)"/><path d="M4 20h9M2 27h10M4 34h9"/></svg>
      </span></div>
      <p><b>Quick</b>&nbsp;and<br><b>Easy</b></p>
    </div>
  </section>

  <div class="brand"><span class="brand-mark"></span><span>Keystone<br>Lending Group</span></div>

  <div class="contact-bar">
    <span class="label">CONTACT US TODAY</span>
    <span class="phone">
      <svg width="24" height="24" viewBox="0 0 24 24"><circle cx="12" cy="12" r="11" fill="#fff"/><path d="M8 6l2 0 1 3-1.5 1.2a7 7 0 0 0 4.3 4.3L15 13l3 1v2c0 1-1 2-2 2A11 11 0 0 1 6 8c0-1 1-2 2-2z" fill="var(--red)"/></svg>
      555 0142 7781
    </span>
  </div>

  <address class="address">
    <svg class="pin" width="18" height="22" viewBox="0 0 18 22"><path d="M9 1a7 7 0 0 1 7 7c0 5-7 12-7 12S2 13 2 8a7 7 0 0 1 7-7z" fill="var(--green)"/><circle cx="9" cy="8" r="2.6" fill="#fff"/></svg>
    <span class="branch">Austin – Meadow Ridge</span><br>
    2180-4 Meadow Ridge Ave<br>
    Austin, Texas 78701
  </address>
</main>
</body>
</html>
```